Wordpress Design Project

Hi,

I would like a more modern colourful design doing for my website ZAP Lnx (www.za%plnx.com - remove percentage). But I do still want to keep the same sort of colors, just maybe lighter. More interesting.

I want the inside pages to NOT all look the same with just boring text.

I want the site to look more appealing and maybe a new logo.
Updates

I would like to mention I would prefer to keep the same logo after rethinking it (possibly a slight refresh of the logo if you feel its a good idea) and the same color scheme as at present.

Saves us rebranding a lot of our apps, tools online ads etc.

Also I thought it is worth mentioning we have 2 parts to the site. The front end and the logged in area. It would be good if when making the front end you keep in mind the back end at http://p.za%plnx.com (remove percentage). We can only edit this limitedly (can edit the entire footer, the logo and full CSS of it). Would be good if we could make sure the header and footer can be used on the back end as well maybe to make it match.

I also want layouts making not just for the homepage. Obviously every page will basically be the same but I don't want all the other pages to just be 'text' and no real layout.

You can see out main pages on the website at the moment, I want those other pages to be laid out nice and differently as well. For example the testimonials page could be more interesting with speech bubbles and pictures of each person (just use placeholders). The affiliates page could be a description and then a nice fancy list of features why to join etc. 

Nothing overly complicated but I think it makes the whole site seem a lot better.

Target Market(s)

Affiliate Marketing. International.

Requirements
Must have
• Needs to be more room for links across the navigation at the top, also sub menus (at present we have a lot of pages which are hidden deep within other pages).
Nice to have
• Lists of features for advertisers and affiliates on the homepage part.

Menu items and buttons have nice hover over effects.

I want to get across on our pages all the different unique features we have.

Maybe some kind of slider which has past offer logos in, just use example logos.

```html
<!DOCTYPE html>
<html lang="en">
<head>
<meta charset="utf-8">
<title>ZAP Lnx – International Affiliate Network</title>
<link href="https://fonts.googleapis.com/css2?family=Arimo:ital,wght@0,400;0,700;1,400&display=swap" rel="stylesheet">
<style>
:root{
  --page-bg:#f1f1f1;
  --blue-dark:#1f6fa5;
  --blue-mid:#2f86c0;
  --blue-light:#5fb0dc;
  --orange:#f28a16;
  --orange-dark:#e0650a;
  --heading-blue:#1d6fa8;
  --text:#555;
  --grey-btn-top:#a9abae;
  --grey-btn-bot:#7c7f83;
  --footer-bg:#3b3b3b;
  --footer-text:#e6e6e6;
  --white:#fff;
}
*{box-sizing:border-box;margin:0;padding:0}
html,body{width:1200px;height:1127px;overflow:hidden}
body{background:var(--page-bg);font-family:"Arimo",Arial,sans-serif;color:var(--text);position:relative}
.page{position:absolute;left:91px;top:0;width:1018px;height:1127px;background:#fafafa;border-left:1px solid #ddd;border-right:1px solid #ddd}
.abs{position:absolute}

/* header */
.masthead{position:absolute;left:95px;top:4px;width:1010px;height:516px;
  background:linear-gradient(100deg,var(--blue-dark) 0%,var(--blue-mid) 30%,var(--blue-light) 55%,var(--blue-mid) 80%,var(--blue-dark) 100%)}
.brand{left:16px;top:32px;font-size:40px;font-weight:700;color:var(--white);line-height:48px}
.toplinks{right:14px;top:20px;color:var(--white);font-size:14.5px;display:flex;gap:10px;align-items:baseline}
.toplinks .call{font-weight:700;font-size:17px}
.search{right:14px;top:56px;width:219px;height:30px;background:var(--white);border:1px solid #bbb;font-size:11.5px;color:#666;padding:8px 11px}
.search svg{position:absolute;right:8px;top:7px}

.nav{position:absolute;left:8px;top:114px;width:994px;height:52px;display:flex;
  background:linear-gradient(#f9a63a,#f28a16 55%,#e8760d);border-radius:3px}
.nav a{height:52px;display:flex;align-items:center;justify-content:center;color:var(--white);font-weight:700;font-size:14.5px;text-decoration:none;border-right:1px solid #f7b361;text-shadow:0 1px 1px rgba(0,0,0,.25)}
.nav a.active{background:linear-gradient(#f07a1a,#dd5a06)}

.hero{position:absolute;left:8px;top:173px;width:994px;height:334px;background:var(--white);border-radius:3px}
.hero h1{position:absolute;left:34px;top:48px;font-size:25px;line-height:30px;color:var(--heading-blue);font-weight:700}
.hero p{position:absolute;left:34px;width:450px;font-size:13.5px;line-height:23px;color:var(--text)}
.hero .lead{top:88px}
.hero .lead span{color:var(--orange-dark)}
.hero .more{top:166px}
.btn{display:flex;align-items:center;justify-content:center;color:var(--white);font-weight:700;border-radius:3px;
  background:linear-gradient(var(--grey-btn-top),var(--grey-btn-bot));border:1px solid #6f7276;text-shadow:0 1px 1px rgba(0,0,0,.35)}
.hero .btn{position:absolute;left:35px;top:234px;width:113px;height:38px;font-size:15px}
.dots{position:absolute;left:35px;top:297px;display:flex;gap:8px}
.dots i{width:14px;height:14px;border-radius:50%;background:#3b3b3b}
.dots i.on{background:var(--orange-dark)}
.hero-art{position:absolute;left:554px;top:37px;width:397px;height:262px;border-radius:6px;
  background:radial-gradient(ellipse at 50% 55%,#8c9a82 0%,#c8d0c2 45%,#fff 75%)}

/* intro */
.intro{left:121px;top:546px;width:962px;font-style:italic;font-size:14.5px;line-height:23px;color:#888}
.rule{left:105px;top:632px;width:990px;height:1px;background:#e2e2e2}

/* feature cards */
.card{position:absolute;left:105px;width:662px;background:var(--white);border:1px solid #e4e4e4;box-shadow:inset 0 0 12px rgba(0,0,0,.06)}
.card .art{position:absolute;left:14px;top:20px;width:152px;height:122px;border-radius:8px}
.card h2{position:absolute;left:190px;top:19px;font-size:18px;color:var(--heading-blue)}
.card p{position:absolute;left:190px;top:44px;width:452px;font-size:13.5px;line-height:23px;color:var(--text);text-align:justify}
.card .btn{position:absolute;left:190px;top:124px;width:124px;height:30px;font-size:15px}
.card-aff{top:657px;height:173px}
.card-aff .art{background:linear-gradient(#8fb3d6,#5c8cc0)}
.card-adv{top:846px;height:172px}
.card-adv .art{background:radial-gradient(circle at 50% 45%,#e6c33a,#b0b0b0 55%,#fff 80%)}

/* sidebar */
.panel{position:absolute;left:783px;width:313px;background:linear-gradient(#f0f0f0,#dcdcdc);border:1px solid #cfcfcf;border-radius:3px}
.panel h3{position:absolute;left:48px;font-size:18.5px;color:var(--heading-blue)}
.panel .ico{position:absolute;left:12px}
.login{top:657px;height:191px}
.login h3{top:20px}
.login .head-rule{position:absolute;left:0;top:52px;width:100%;height:1px;background:#cfcfcf}
.field-label{position:absolute;right:231px;font-size:12.5px;color:#555}
.field{position:absolute;left:83px;width:217px;height:31px;background:var(--white);border:1px solid #c8c8c8}
.login .btn{position:absolute;left:221px;top:146px;width:77px;height:31px;font-size:14px;background:linear-gradient(#5a5a5a,#2e2e2e);border-color:#222}
.news{top:857px;height:160px}
.news h3{top:20px}
.news .next{position:absolute;right:16px;top:22px}
.news-body{position:absolute;left:7px;top:53px;width:297px;height:100px;background:var(--white);border:1px solid #d3d3d3}
.news-body .title{position:absolute;left:28px;top:16px;font-size:13.5px;color:var(--orange-dark)}
.news-body .mark{position:absolute;left:10px;top:14px;font-size:15px;color:var(--orange-dark)}
.news-body p{position:absolute;left:28px;top:40px;width:260px;font-size:13px;line-height:19px;color:#555}

/* footer */
.footer{position:absolute;left:95px;top:1032px;width:1010px;height:95px;background:var(--footer-bg);color:var(--footer-text);font-size:12.5px}
.footer .links{position:absolute;left:16px;top:24px;display:flex;gap:11px}
.footer .copy{position:absolute;left:16px;top:60px;word-spacing:1px}
.social{position:absolute;left:936px;top:35px;display:flex;gap:8px}
.social i{width:25px;height:25px;border-radius:4px;background:#4a6fb0}
.social i + i{background:#4aaee3}
</style>
</head>
<body>
<div class="page"></div>

<header class="masthead">
  <div class="abs brand">ZAP Lnx</div>
  <div class="abs toplinks"><span>REGISTER</span><span>|</span><span>SIGN IN</span><span>&nbsp;|&nbsp;</span><span class="call">Call us : +44 (0)1632 960418</span></div>
  <div class="abs search">Search
    <svg width="16" height="16" viewBox="0 0 16 16"><circle cx="6" cy="6" r="4.5" fill="none" stroke="#222" stroke-width="2"/><line x1="9.5" y1="9.5" x2="14.5" y2="14.5" stroke="#222" stroke-width="3" stroke-linecap="round"/></svg>
  </div>

  <nav class="nav">
    <a class="active" style="width:111px">HOME</a>
    <a style="width:132px">ABOUT US</a>
    <a style="width:133px">OUR BLOG</a>
    <a style="width:163px">TESTIMONIALS</a>
    <a style="width:136px">AFFILIATES</a>
    <a style="width:161px">ADVERTISERS</a>
    <a style="width:158px;border-right:none">CONTACT US</a>
  </nav>

  <section class="hero">
    <h1>International Affiliate Network</h1>
    <p class="lead"><span>Welcome to the ZAP Lnx affiliate network.</span> On time payments, hot &amp; exclusive CPL/CPA offers, fast support and low fees for advertisers, is the making of a leading affiliate network!</p>
    <p class="more">ZAP Lnx offer a wide range of advertisers for your websites. So you can start monetizing your traffic or get an additional revenue stream, today.</p>
    <a class="btn">View more</a>
    <div class="dots"><i class="on"></i><i></i><i></i><i></i></div>
    <div class="hero-art" role="img" aria-label="Laptop with banknotes flying out of the screen"></div>
  </section>
</header>

<p class="abs intro">ZAP Lnx Affiliate Network we focus on lead generation offers. We have a range of competitions, surveys, incentives and gambling offers. Whatever the industry, you will be able to find offers to suit your traffic.ZAP Lnx is a powerful performance-based internet marketing network dedicated to advertisers to affiliates through its powerful affiliate network..</p>
<div class="abs rule"></div>

<section class="card card-aff">
  <div class="art" role="img" aria-label="Group of three business people"></div>
  <h2>Affiliates</h2>
  <p>Get access to a wide range of top performing offers for your websites and email marketing lists. Fresh and exclusive offers to promote. Join over 2,000 affiliates already signed up to ZAP Lnx.</p>
  <a class="btn">Sign up Now</a>
</section>

<section class="card card-adv">
  <div class="art" role="img" aria-label="Yellow and silver megaphone"></div>
  <h2>Advertisers</h2>
  <p>Generate sales/leads to your website instantly with the ZAP Lnx Affiliate Network. Only pay on performance, no monthly or setup fees. ZAP Lnx takes the risk out of advertising.</p>
  <a class="btn">Sign up Now</a>
</section>

<aside class="panel login">
  <svg class="ico" style="top:9px" width="26" height="32" viewBox="0 0 26 32"><path d="M6 14V9a7 7 0 0 1 14 0v5" fill="none" stroke="#8a9098" stroke-width="3"/><rect x="2" y="14" width="22" height="16" rx="2" fill="#a9b0b8"/></svg>
  <h3>Account Login</h3>
  <div class="head-rule"></div>
  <span class="field-label" style="top:70px">Email :</span>
  <div class="field" style="top:62px"></div>
  <span class="field-label" style="top:109px">Password :</span>
  <div class="field" style="top:101px"></div>
  <a class="btn">LOG IN</a>
</aside>

<aside class="panel news">
  <svg class="ico" style="top:14px" width="28" height="24" viewBox="0 0 28 24"><rect x="2" y="12" width="4" height="10" fill="#a9b0b8"/><rect x="8" y="6" width="4" height="16" fill="#a9b0b8"/><rect x="14" y="9" width="4" height="13" fill="#a9b0b8"/><rect x="20" y="3" width="4" height="19" fill="#a9b0b8"/><line x1="0" y1="23" x2="28" y2="23" stroke="#8a9098" stroke-width="2"/></svg>
  <h3>Latest News</h3>
  <svg class="next" width="18" height="18" viewBox="0 0 18 18"><circle cx="9" cy="9" r="8" fill="#8d8d8d"/><path d="M7.5 5.5 11 9l-3.5 3.5" fill="none" stroke="#fff" stroke-width="2"/></svg>
  <div class="news-body">
    <span class="mark">»</span>
    <span class="title">Curabitur congue odio vitae</span>
    <p>Ligula semper ac auctor justo tincidunt. unc placerat sodales massa non molestie.</p>
  </div>
</aside>

<footer class="footer">
  <div class="links"><span>Home</span><span>|</span><span>About Us</span><span>|</span><span>Our Blog</span><span>|</span><span>Testimonials</span><span>|</span><span>Affiliates</span><span>|</span><span>Advertisers</span><span>|</span><span>Contact Us</span></div>
  <div class="copy">Copyright &nbsp;©&nbsp; 2013 &nbsp;&nbsp; www.zaplnx.com &nbsp;&nbsp; All rights reserved.</div>
  <div class="social"><i></i><i></i></div>
</footer>
</body>
</html>
```